Refer a Friend A5 Flyer for Healthcare Staff

We need an A5 flyer that we can hand out to existing and new staff members promoting our Refer a friend Scheme. We need the leaflet to encourage staff to talk to their family and friends about joining our Healthcare Agency, which provides staff to local care related establishments. Using our logo and brand colours blue and green, as per our website, the final design will need to clearly convey the benefits and attractions of referring additional staff to the team. In addition is the promotion of our Chatterbook page, requesting staff to like the page and to like and share various posts.

Target Market(s)

Healthcare and potential Healthcare Staff

Industry/Entity Type

Healthcare

Colors
33b8a4
3277b5

Requirements
Must have
• Company Logo, Brand colours,
• text; "Refer a Friend and receive a £50 Bonus after just 1 completed shift"
• text; "3 easy steps to refer a friend, 1 Fill out your name on the back of your Business Card 2 Hand the card to your friend or any person you wish to refer, 3 ask your friend to present the card to us when they attend their interview"
• text; "Like and share any of our Open Days on Chatterbook for a chance to win a prize, you can find us easily by searching @CarewellStaffingPartners"
• text; "Like our Page to stay up to date with our events and offers"
Nice to have
• care worker / elderly care / support worker pictures
• Content / pics from website www.carewellstaffingpartners.co.uk

```html
<!DOCTYPE html>
<html lang="en">
<head>
<meta charset="utf-8">
<title>Carewell Staffing Partners – Refer a Friend Flyer</title>
<link href="https://fonts.googleapis.com/css2?family=Poppins:ital,wght@0,300;0,400;0,500;0,600;0,700;1,400&display=swap" rel="stylesheet">
<style>
  :root{
    --brand-blue:#1454a6;
    --brand-blue-dark:#0f4896;
    --brand-teal:#22a98f;
    --brand-teal-light:#4cc2ac;
    --page-bg:#e9ecef;
    --paper:#ffffff;
    --ink-blue:#1a4f9e;
  }
  *{margin:0;padding:0;box-sizing:border-box}
  html,body{width:1099px;height:1200px;overflow:hidden}
  body{
    background:var(--page-bg);
    font-family:'Poppins',sans-serif;
    position:relative;
  }
  .flyer{
    position:absolute;left:135px;top:12px;
    width:828px;height:1175px;
    background:var(--paper);
    box-shadow:0 4px 14px rgba(0,0,0,.18);
    overflow:hidden;
  }
  .hero{
    position:absolute;left:0;top:0;width:828px;height:488px;
    background:
      radial-gradient(ellipse 55% 60% at 72% 28%, #fbfcf7 0%, rgba(245,247,236,.9) 45%, rgba(245,247,236,0) 80%),
      linear-gradient(180deg, rgba(0,0,0,0) 60%, rgba(226,200,70,.55) 100%),
      linear-gradient(90deg, #6d8f4e 0%, #9cb4c9 22%, #c7d3dc 38%, #dfe6d2 60%, #e9ecd8 100%);
  }
  .brand{
    position:absolute;left:400px;top:120px;width:370px;
    display:flex;align-items:center;gap:14px;
  }
  .brand-dot{
    width:22px;height:22px;border-radius:50%;background:var(--brand-teal);flex:none;
  }
  .brand-name{
    font-weight:400;font-size:40px;line-height:1.05;color:var(--brand-blue);
  }
  .tagline{
    position:absolute;left:400px;right:66px;top:224px;text-align:right;
    font-weight:300;font-size:16px;color:#6b7178;
  }
  .values{
    position:absolute;left:300px;width:556px;top:285px;
    display:flex;flex-direction:column;align-items:center;gap:6px;
  }
  .value-tag{
    background:var(--brand-teal);color:#fff;
    font-weight:400;font-size:27px;line-height:32px;padding:0 4px;
    letter-spacing:.2px;
  }
  .offer-band{
    position:absolute;left:0;top:488px;width:828px;height:267px;
    background:var(--brand-blue);
    border-top:8px solid var(--brand-teal);
    border-bottom:8px solid var(--brand-teal);
    display:flex;align-items:center;justify-content:center;
  }
  .offer-headline{
    color:#fff;text-align:center;font-weight:500;font-size:57px;line-height:62px;
  }
  .offer-headline strong{font-weight:700}
  .steps{
    position:absolute;left:0;top:786px;width:828px;text-align:center;color:var(--ink-blue);
  }
  .steps-title{font-weight:600;font-size:39px;line-height:50px}
  .steps-list{list-style:none;font-weight:400;font-size:18px;line-height:23px}
  .social-box{
    position:absolute;left:30px;top:945px;width:763px;height:194px;
    border:4px solid var(--brand-teal);border-radius:14px;overflow:hidden;
    display:flex;flex-direction:column;
  }
  .social-prize{
    display:block;
    height:136px;flex:none;
    padding-top:16px;
    background:linear-gradient(180deg,var(--brand-teal-light) 0%,var(--brand-teal) 42%,#1ea58b 100%);
    color:#fff;text-align:center;font-weight:400;font-size:26px;line-height:34px;
    white-space:nowrap;
  }
  .social-prize strong{font-weight:700}
  .social-follow{
    flex:1;background:var(--brand-blue-dark);color:#fff;
    font-style:italic;font-weight:400;font-size:23px;
    display:flex;align-items:center;justify-content:center;
    white-space:nowrap;
  }
</style>
</head>
<body>
  <article class="flyer">
    <div class="hero" role="img" aria-label="Photo of a smiling carer standing behind an elderly man in a wheelchair in a sunny flower garden"></div>

    <div class="brand">
      <span class="brand-dot"></span>
      <span class="brand-name">Carewell Staffing Partners</span>
    </div>
    <p class="tagline">Keeping it Simple</p>

    <div class="values">
      <span class="value-tag">SIMPLICITY</span>
      <span class="value-tag">SUPERIOR SOLUTIONS</span>
      <span class="value-tag">OFFICIALLY RECOGNIZED</span>
    </div>

    <section class="offer-band">
      <h1 class="offer-headline">Refer a Friend and<br>receive a <strong>£50</strong> Bonus after<br>just 1 completed shift</h1>
    </section>

    <section class="steps">
      <h2 class="steps-title">3 easy steps to refer a friend</h2>
      <ol class="steps-list">
        <li>1. Fill out your name on the back of your Business Card</li>
        <li>2. Hand the card to your friend or any person you wish to refer</li>
        <li>3. ask your friend to present the card to us when they attend their interview</li>
      </ol>
    </section>

    <section class="social-box">
      <p class="social-prize">Like and share any of our Open Days on <strong>Chatterbook</strong><br>for a chance to win a prize, you can find us easily<br>by searching <strong>@CarewellStaffingPartners</strong></p>
      <p class="social-follow">Like our Page to stay up to date with our events and offers</p>
    </section>
  </article>
</body>
</html>
```